corvale institute of business and technology web site

I need web site for the institute which focus on business courses and computer course it is also for vocation train for employment It is also carear development and advancement .It should have links to online study resource which free
Industry/Entity Type
Business
Number of Pages Required
1 page
Look and feel
Each slider illustrates characteristics of the customer's brand and the style your logo design should communicate.

```html
<!DOCTYPE html>
<html lang="en">
<head>
<meta charset="utf-8">
<title>Corvale Institute of Business and Technology</title>
<link href="https://fonts.googleapis.com/css2?family=Oswald:wght@400;500;700&family=Open+Sans:wght@400;600;700&display=swap" rel="stylesheet">
<style>
:root{
  --blue:#1d8ad3;
  --blue-dark:#156fae;
  --green:#7cbf3f;
  --ink:#222;
  --muted:#666;
  --dark:#1c1c1c;
  --footer:#202124;
  --white:#fff;
}
*{box-sizing:border-box;margin:0;padding:0}
html,body{width:1200px;height:3348px;overflow:hidden}
body{font-family:"Open Sans",Arial,sans-serif;color:var(--ink);background:var(--white);font-size:14px;line-height:1.6}
h1,h2,h3{font-family:"Oswald","Arial Narrow",sans-serif}
a{color:inherit;text-decoration:none}

/* header */
.site-header{height:100px;position:relative;background:var(--white)}
.brand{position:absolute;left:28px;top:6px;display:flex;align-items:center;gap:12px}
.brand-mark{width:64px;height:64px;border-radius:50%;background:var(--blue)}
.brand-name{font-family:"Oswald",sans-serif;font-weight:700;color:var(--blue-dark);font-size:34px;line-height:1}
.brand-sub{font-family:"Oswald",sans-serif;font-weight:700;color:var(--blue-dark);font-size:11px;letter-spacing:.5px;line-height:1.2;margin-top:4px}
.topbar{position:absolute;right:28px;top:8px;display:flex;gap:34px;font-size:12px;color:var(--muted)}
.topbar .item{display:flex;gap:8px;align-items:center;line-height:1.3}
.topbar b{display:block;color:var(--blue);font-size:11px}
.socials{display:flex;gap:6px}
.socials span{width:22px;height:22px;border-radius:50%;background:var(--blue)}
.main-nav{position:absolute;left:440px;right:0;top:48px;height:36px;background:var(--blue);display:flex;align-items:center;padding:0 20px}
.main-nav a{color:var(--white);font-weight:700;font-size:12px;margin-right:34px}
.main-nav .search{margin-left:auto;width:230px;height:24px;background:var(--white);font-size:11px;color:#999;padding:3px 10px}

/* hero */
.hero{height:600px;position:relative;background:linear-gradient(180deg,#5b5650 0%,#3c3a38 45%,#2a2a2a 100%);color:var(--white);text-align:center}
.hero h1{padding-top:248px;font-size:54px;font-weight:700;letter-spacing:3px;line-height:1.1}
.hero p{font-family:"Oswald",sans-serif;font-size:26px;margin-top:14px}
.hero .btn{display:inline-block;margin-top:40px;background:var(--blue);padding:10px 32px;font-weight:700;font-size:14px}
.hero .arrows{position:absolute;right:18px;bottom:28px;display:flex;gap:4px}
.hero .arrows span{width:40px;height:40px;background:rgba(0,0,0,.7);display:flex;align-items:center;justify-content:center}

/* welcome */
.welcome{height:320px;display:flex;padding:40px 28px 0 52px;gap:40px}
.welcome-text{flex:1}
.welcome-text h2{font-size:22px;color:var(--blue-dark);line-height:1.2;font-weight:700}
.welcome-text h2 small{display:block;font-size:22px}
.rule{width:110px;height:3px;background:var(--blue);margin:10px 0 16px}
.welcome-text p{font-size:14px;color:#444;line-height:1.75;text-align:justify}
.video-box{width:260px;border:1px solid #ddd;padding:12px;height:250px}
.video-box h3{font-size:16px;font-weight:700;border-bottom:2px solid var(--blue);padding-bottom:4px;margin-bottom:10px}
.video-thumb{height:140px;background:linear-gradient(135deg,#7aa6c8,#c9d7e2);display:flex;align-items:center;justify-content:center}
.video-box p{font-size:13px;color:#444;margin-top:8px;line-height:1.5}

/* programs */
.programs{height:760px;background:linear-gradient(160deg,#2b2b2b,#141414);color:var(--white);text-align:center;padding-top:70px}
.programs h2{font-size:34px;color:var(--blue);line-height:1.05;font-weight:700}
.programs .rule{margin:14px auto 0;width:80px}
.program-grid{display:grid;grid-template-columns:repeat(3,300px);justify-content:center;row-gap:70px;margin-top:60px}
.program svg{display:block;margin:0 auto}
.program h3{font-family:"Open Sans",sans-serif;font-size:16px;font-weight:600;margin-top:14px;line-height:1.3;min-height:42px}
.program .more{display:inline-block;margin-top:18px;font-size:11px;font-weight:700;color:var(--blue);border-bottom:1px solid var(--blue)}

/* online study */
.study{height:420px;display:flex}
.study-photo{width:560px;background:linear-gradient(90deg,#e9e9e9,#d4d4d4)}
.study-panel{flex:1;background:var(--green);padding:72px 0 0 130px}
.study-panel h2{font-size:68px;line-height:1;font-weight:700;color:var(--dark)}
.study-panel h3{font-size:44px;line-height:1.1;font-weight:500;color:var(--dark)}
.study-panel .btn{display:inline-block;margin-top:20px;background:var(--dark);color:var(--white);font-family:"Oswald",sans-serif;font-weight:700;font-size:30px;padding:4px 28px;border-radius:30px}

/* testimonials */
.testimonials{height:600px;text-align:center;padding-top:56px}
.testimonials h2{font-size:28px;color:var(--blue);font-weight:700}
.testimonials .rule{margin:6px auto 0;width:70px}
.quotes{display:flex;gap:20px;padding:0 64px;margin-top:44px;text-align:left}
.quote{flex:1}
.quote .card{border:1px solid #ddd;padding:26px 26px;font-size:13px;color:#555;height:250px;position:relative;line-height:1.75}
.quote .card:before{content:"\201C";position:absolute;left:8px;top:-4px;font-size:40px;color:#333}
.quote .card:after{content:"\201D";position:absolute;right:10px;bottom:-24px;font-size:40px;color:#333}
.person{display:flex;align-items:center;gap:12px;margin-top:26px}
.avatar{width:44px;height:44px;border-radius:50%;background:#c7b8a8}
.person b{font-size:13px;display:block}
.person span{font-size:11px;color:var(--muted)}

/* mailing */
.mailing{height:64px;background:var(--green);display:flex;align-items:center;justify-content:center;gap:24px}
.mailing h3{font-size:22px;font-weight:500;color:var(--dark)}
.mailing .field{width:300px;height:32px;background:var(--white);font-size:12px;color:#999;padding:6px 12px}
.mailing .btn{background:var(--dark);color:var(--white);font-weight:700;font-size:12px;padding:7px 20px;letter-spacing:1px}

/* footer */
.contact-bar{height:76px;background:var(--blue);display:flex;align-items:center;color:var(--white)}
.contact-bar h3{background:var(--blue-dark);height:76px;display:flex;align-items:center;padding:0 36px;font-size:22px;font-weight:500;white-space:nowrap}
.contact-bar .c{display:flex;gap:10px;align-items:center;margin-left:34px;font-size:12px;line-height:1.4;white-space:nowrap}
.contact-bar .c b{display:block;font-size:13px}
.footer{height:362px;background:var(--footer);color:#bbb;display:grid;grid-template-columns:230px 240px 250px 1fr;gap:30px;padding:34px 40px 0 52px;font-size:12px}
.footer h4{color:var(--white);font-size:13px;font-weight:700;border-bottom:1px solid #444;padding-bottom:6px;margin-bottom:10px}
.footer li{list-style:none;line-height:1.9}
.footer .news li{line-height:1.45;margin-bottom:10px}
.footer .news b{color:var(--blue);font-weight:600;display:block}
.footer .socials span{width:28px;height:28px;background:#444}
.partner{margin-top:30px;color:var(--white);font-family:"Oswald",sans-serif;font-size:20px;line-height:1.2}
.partner .badge{display:inline-block;width:50px;height:50px;background:var(--white);margin-top:10px}
.partner .pname{font-size:18px;font-weight:700;margin-top:6px}
.copyright{height:46px;background:#151515;color:#888;font-size:11px;text-align:center;line-height:46px}
</style>
</head>
<body>

<header class="site-header">
  <div class="brand">
    <div class="brand-mark"></div>
    <div>
      <div class="brand-name">CORVALE</div>
      <div class="brand-sub">INSTITUTE OF BUSINESS &amp; TECHNOLOGY</div>
    </div>
  </div>
  <div class="topbar">
    <div class="item">
      <svg width="16" height="16" viewBox="0 0 24 24"><path fill="#1d8ad3" d="M6.6 10.8a15 15 0 0 0 6.6 6.6l2.2-2.2c.3-.3.7-.4 1-.2 1.1.4 2.3.6 3.6.6.6 0 1 .4 1 1V20c0 .6-.4 1-1 1A17 17 0 0 1 3 4c0-.6.4-1 1-1h3.5c.6 0 1 .4 1 1 0 1.3.2 2.5.6 3.6.1.3 0 .7-.2 1z"/></svg>
      <div><b>CALL US</b>+260 555 014 200</div>
    </div>
    <div class="item">
      <svg width="16" height="16" viewBox="0 0 24 24"><path fill="#1d8ad3" d="M2 5h20v14H2zm2 2v.5l8 5 8-5V7z"/></svg>
      <div><b>EMAIL US</b>info@corvaleinstitute.edu</div>
    </div>
    <div class="socials"><span></span><span></span><span></span><span></span><span></span></div>
  </div>
  <nav class="main-nav">
    <a href="#">HOME</a><a href="#">ABOUT US</a><a href="#">COURSES</a><a href="#">CONTACT US</a>
    <div class="search">Search</div>
  </nav>
</header>

<section class="hero" role="img" aria-label="Slider photo of a desk with a keyboard, laptop and coffee">
  <h1>LOREM IPSUM DOLOR SIT AMET</h1>
  <p>Lorem ipsum dolor sit amet, consectetur adipiscing elit, sed do eiusmod tempor.</p>
  <a class="btn" href="#">LEARN MORE</a>
  <div class="arrows">
    <span><svg width="12" height="16" viewBox="0 0 12 16"><path d="M9 2 3 8l6 6" stroke="#fff" stroke-width="3" fill="none"/></svg></span>
    <span><svg width="12" height="16" viewBox="0 0 12 16"><path d="m3 2 6 6-6 6" stroke="#fff" stroke-width="3" fill="none"/></svg></span>
  </div>
</section>

<section class="welcome">
  <div class="welcome-text">
    <h2>WELCOME TO<small>CORVALE INSTITUTE OF BUSINESS AND TECHNOLOGY</small></h2>
    <div class="rule"></div>
    <p>Corvale Institute of Business and Technology (CIBT) is a fast-growing Education &amp; Training Solutions Provider, focusing on holistic knowledge and skills interventions that impact livelihoods. It is established on the core values of making a meaningful and measurable difference to career aspirations and goals through innovative learning and knowledge management intervention. CIBT prepares students not only for professional careers but also inculcates the important virtues of discipline and equips them physically, mentally, socially and spiritually. The Institution is licensed and registered under the National Skills and Career Training Council.</p>
  </div>
  <aside class="video-box">
    <h3>FEATURED VIDEO</h3>
    <div class="video-thumb" role="img" aria-label="Video still of a classroom session">
      <svg width="44" height="44" viewBox="0 0 44 44"><circle cx="22" cy="22" r="21" fill="#1d8ad3"/><path d="M17 13v18l14-9z" fill="#fff"/></svg>
    </div>
    <p>Lorem ipsum dolor sit amet, consectetur adipiscing elit.</p>
  </aside>
</section>

<section class="programs">
  <h2>OUR PROGRAMS<br>OFFERED</h2>
  <div class="rule"></div>
  <div class="program-grid">
    <div class="program">
      <svg width="70" height="70" viewBox="0 0 70 70"><circle cx="35" cy="35" r="33" fill="#1a1a1a" stroke="#1d8ad3" stroke-width="2"/><path d="M18 31l17-8 17 8-17 8z" fill="#fff"/><path d="M25 35v8c5 4 15 4 20 0v-8" fill="none" stroke="#fff" stroke-width="2"/></svg>
      <h3>University Education -<br>Long Distance Learning</h3><a class="more" href="#">FIND OUT MORE</a>
    </div>
    <div class="program">
      <svg width="70" height="70" viewBox="0 0 70 70"><circle cx="35" cy="35" r="33" fill="#1a1a1a" stroke="#1d8ad3" stroke-width="2"/><rect x="21" y="21" width="12" height="12" fill="#fff"/><rect x="37" y="21" width="12" height="12" fill="#fff"/><rect x="21" y="37" width="12" height="12" fill="#fff"/><rect x="37" y="37" width="12" height="12" fill="#1d8ad3"/></svg>
      <h3>Modular<br>Soft Skills</h3><a class="more" href="#">FIND OUT MORE</a>
    </div>
    <div class="program">
      <svg width="70" height="70" viewBox="0 0 70 70"><circle cx="35" cy="35" r="33" fill="#1a1a1a" stroke="#1d8ad3" stroke-width="2"/><rect x="18" y="22" width="34" height="22" fill="none" stroke="#fff" stroke-width="2"/><path d="M28 50h14M35 44v6" stroke="#fff" stroke-width="2"/></svg>
      <h3>Direct to Device<br>(D2D)</h3><a class="more" href="#">FIND OUT MORE</a>
    </div>
    <div class="program">
      <svg width="70" height="70" viewBox="0 0 70 70"><circle cx="35" cy="35" r="33" fill="#1a1a1a" stroke="#1d8ad3" stroke-width="2"/><circle cx="35" cy="35" r="14" fill="none" stroke="#fff" stroke-width="2"/><path d="M21 35h28M35 21v28" stroke="#fff" stroke-width="2"/></svg>
      <h3>Brightpath</h3><a class="more" href="#">FIND OUT MORE</a>
    </div>
    <div class="program">
      <svg width="70" height="70" viewBox="0 0 70 70"><circle cx="35" cy="35" r="33" fill="#1a1a1a" stroke="#1d8ad3" stroke-width="2"/><path d="M20 48V38h7v10M31 48V30h7v18M42 48V22h7v26" fill="#fff"/></svg>
      <h3>Brightpath Roles In<br>The Talent Continuum</h3><a class="more" href="#">FIND OUT MORE</a>
    </div>
    <div class="program">
      <svg width="70" height="70" viewBox="0 0 70 70"><circle cx="35" cy="35" r="33" fill="#1a1a1a" stroke="#1d8ad3" stroke-width="2"/><rect x="20" y="28" width="30" height="20" fill="#fff"/><path d="M29 28v-5h12v5" fill="none" stroke="#fff" stroke-width="2"/></svg>
      <h3>Business Verticals</h3><a class="more" href="#">FIND OUT MORE</a>
    </div>
  </div>
</section>

<section class="study">
  <div class="study-photo" role="img" aria-label="Photo of a student lying on the floor studying on a laptop"></div>
  <div class="study-panel">
    <h2>ONLINE STUDY</h2>
    <h3>RESOURCE WHICH FREE</h3>
    <a class="btn" href="#">CLICK HERE</a>
  </div>
</section>

<section class="testimonials">
  <h2>WHAT OTHER SAYS TESTIMONIALS</h2>
  <div class="rule"></div>
  <div class="quotes">
    <div class="quote">
      <div class="card">Lorem ipsum dolor sit amet, consectetur adipiscing elit, sed do eiusmod tempor incididunt ut labore et dolore magna aliqua. Ut enim ad minim veniam, quis nostrud exercitation ullamco laboris nisi ut aliquip ex ea commodo consequat. Duis aute irure dolor in reprehenderit in voluptate velit esse cillum dolore.</div>
      <div class="person"><div class="avatar" role="img" aria-label="Portrait of Daniel Mwale"></div><div><b>Daniel Mwale</b><span>Student</span></div></div>
    </div>
    <div class="quote">
      <div class="card">Lorem ipsum dolor sit amet, consectetur adipiscing elit, sed do eiusmod tempor incididunt ut labore et dolore magna aliqua. Ut enim ad minim veniam, quis nostrud exercitation ullamco laboris nisi ut aliquip ex ea commodo consequat. Duis aute irure dolor in reprehenderit in voluptate velit esse cillum dolore.</div>
      <div class="person"><div class="avatar" role="img" aria-label="Portrait of Ruth Banda"></div><div><b>Ruth Banda</b><span>Student</span></div></div>
    </div>
    <div class="quote">
      <div class="card">Lorem ipsum dolor sit amet, consectetur adipiscing elit, sed do eiusmod tempor incididunt ut labore et dolore magna aliqua. Ut enim ad minim veniam, quis nostrud exercitation ullamco laboris nisi ut aliquip ex ea commodo consequat. Duis aute irure dolor in reprehenderit in voluptate velit esse cillum dolore.</div>
      <div class="person"><div class="avatar" role="img" aria-label="Portrait of Grace Phiri"></div><div><b>Grace Phiri</b><span>Student</span></div></div>
    </div>
  </div>
</section>

<section class="mailing">
  <h3>JOIN OUR MAILING LIST</h3>
  <div class="field">Sign up to our mailing list</div>
  <a class="btn" href="#">SUBSCRIBE</a>
</section>

<footer>
  <div class="contact-bar">
    <h3>GET IN TOUCH</h3>
    <div class="c">
      <svg width="22" height="22" viewBox="0 0 24 24"><path fill="#fff" d="M12 2a7 7 0 0 0-7 7c0 5 7 13 7 13s7-8 7-13a7 7 0 0 0-7-7zm0 9.5A2.5 2.5 0 1 1 12 6a2.5 2.5 0 0 1 0 5.5z"/></svg>
      <div>Plot 24 Meadowbrook Complex,<br>Lakeview Road, Kafue</div>
    </div>
    <div class="c">
      <svg width="22" height="22" viewBox="0 0 24 24"><path fill="#fff" d="M6.6 10.8a15 15 0 0 0 6.6 6.6l2.2-2.2c.3-.3.7-.4 1-.2 1.1.4 2.3.6 3.6.6.6 0 1 .4 1 1V20c0 .6-.4 1-1 1A17 17 0 0 1 3 4c0-.6.4-1 1-1h3.5c.6 0 1 .4 1 1 0 1.3.2 2.5.6 3.6.1.3 0 .7-.2 1z"/></svg>
      <div><b>Call Us</b>+260 555 014 200<br>+260 555 014 201</div>
    </div>
    <div class="c">
      <svg width="22" height="22" viewBox="0 0 24 24"><circle cx="12" cy="12" r="9" fill="none" stroke="#fff" stroke-width="2"/><path d="M3 12h18M12 3c3 3 3 15 0 18M12 3c-3 3-3 15 0 18" fill="none" stroke="#fff" stroke-width="1.5"/></svg>
      <div><b>Website</b>www.corvaleinstitute.edu</div>
    </div>
    <div class="c">
      <svg width="22" height="22" viewBox="0 0 24 24"><path fill="#fff" d="M2 5h20v14H2zm2 2v.5l8 5 8-5V7z"/></svg>
      <div><b>Email</b>info@corvaleinstitute.edu</div>
    </div>
  </div>
  <div class="footer">
    <div>
      <h4>NAVIGATION</h4>
      <ul><li>Home</li><li>About Us</li><li>Courses</li><li>Contact Us</li></ul>
    </div>
    <div>
      <h4>PROGRAMS OFFERED</h4>
      <ul><li>University Education - Long Distance</li><li>Modular Soft Skills</li><li>Direct to Device (D2D)</li><li>Brightpath</li><li>Brightpath Roles In The Talent Continuum</li><li>Business Verticals</li></ul>
    </div>
    <div class="news">
      <h4>RECENT NEWS</h4>
      <ul>
        <li><b>January 28, 2015</b>Lorem ipsum dolor sit amet, consectetur adipiscing elit.</li>
        <li><b>January 28, 2015</b>Lorem ipsum dolor sit amet, consectetur adipiscing elit.</li>
        <li><b>January 28, 2015</b>Lorem ipsum dolor sit amet, consectetur adipiscing elit.</li>
      </ul>
    </div>
    <div>
      <h4>FOLLOW US</h4>
      <div class="socials"><span></span><span></span><span></span><span></span><span></span></div>
      <div class="partner">
        IN CONJUNCTION<br>WITH BRIGHTPATH
        <div><span class="badge"></span></div>
        <div class="pname">BRIGHTPATH</div>
      </div>
    </div>
  </div>
  <div class="copyright">© 2015 Corvale Institute of Business and Technology. All Rights Reserved.</div>
</footer>

</body>
</html>
```